Business Cards for a law firm

Business cards for our law firm. Use our silhoette logo and OAK PARTNERS - check our website (www.oakpartners.example)

Contact Information for Business Card

our silhouette logo, OAK PARTNERS, 800-555-0147, Dorian Pemberton, dorian@oakpartners.example

Requirements
Must have
• our silhouette logo, OAK PARTNERS, 800-555-0147, Dorian Pemberton, dorian@oakpartners.example

```html
<!DOCTYPE html>
<html lang="en">
<head>
<meta charset="utf-8">
<title>Oak Partners — Business Cards</title>
<link rel="stylesheet" href="https://fonts.googleapis.com/css2?family=Bebas+Neue&family=Montserrat:wght@400;500;600&display=swap">
<style>
  :root {
    --backdrop: #2b2b2d;
    --card-navy: #1b2f6b;
    --accent-amber: #f7a824;
    --ink-white: #ffffff;
    --rule-grey: #8c97b8;
  }
  * { box-sizing: border-box; margin: 0; padding: 0; }
  html, body {
    width: 1200px; height: 1108px; overflow: hidden;
    background: var(--backdrop);
  }
  .canvas {
    position: relative; width: 1200px; height: 1108px;
  }
  .card {
    position: absolute; top: 204px;
    width: 440px; height: 700px;
    background: var(--card-navy);
    border-radius: 26px;
    overflow: hidden;
  }
  .card--front { left: 120px; }
  .card--back { left: 640px; }

  /* Front */
  .brand {
    position: absolute; top: 170px; left: 0; right: 0;
    display: flex; align-items: center; justify-content: center; gap: 14px;
  }
  .brand__mark {
    width: 22px; height: 22px; border-radius: 50%;
    background: var(--ink-white);
  }
  .brand__name {
    font-family: "Montserrat", sans-serif; font-weight: 500;
    font-size: 30px; letter-spacing: 0.18em;
    color: var(--ink-white);
  }
  .holder-name {
    position: absolute; top: 440px; left: 0; right: 0; text-align: center;
    font-family: "Montserrat", sans-serif; font-weight: 500;
    font-size: 24px; letter-spacing: 0.04em;
    color: var(--accent-amber);
  }
  .contact-rule {
    position: absolute; top: 496px; left: 50px; right: 50px;
    display: flex; align-items: center; gap: 8px;
  }
  .contact-rule__line { flex: 1; height: 1px; background: var(--rule-grey); }
  .contact-rule__icon {
    width: 34px; height: 34px; border-radius: 7px;
    background: var(--ink-white);
    display: flex; align-items: center; justify-content: center;
  }
  .contact-list {
    position: absolute; top: 546px; left: 0; right: 0; text-align: center;
    font-family: "Montserrat", sans-serif; color: var(--ink-white);
  }
  .contact-list__phone { font-size: 28px; font-weight: 500; letter-spacing: 0.03em; line-height: 40px; }
  .contact-list__line { font-size: 19px; line-height: 32px; }

  /* Back */
  .pitch {
    position: absolute; top: 210px; left: 44px; right: 30px;
    font-family: "Bebas Neue", sans-serif; line-height: 0.95;
  }
  .pitch__firm { font-size: 46px; color: var(--accent-amber); }
  .pitch__headline { font-size: 124px; color: var(--ink-white); line-height: 0.9; }
  .pitch__call { font-size: 42px; color: var(--ink-white); margin-top: 6px; }
  .pitch__phone { font-size: 72px; color: var(--accent-amber); margin-top: 8px; }
</style>
</head>
<body>
<main class="canvas">
  <section class="card card--front" aria-label="Business card front">
    <div class="brand">
      <span class="brand__mark"></span>
      <span class="brand__name">OAK PARTNERS</span>
    </div>
    <p class="holder-name">DORIAN PEMBERTON</p>
    <div class="contact-rule">
      <span class="contact-rule__line"></span>
      <span class="contact-rule__icon">
        <svg width="20" height="20" viewBox="0 0 24 24" aria-hidden="true"><path d="M6.6 10.8a15 15 0 0 0 6.6 6.6l2.2-2.2a1 1 0 0 1 1-.25 11.4 11.4 0 0 0 3.6.57 1 1 0 0 1 1 1V20a1 1 0 0 1-1 1A17 17 0 0 1 3 4a1 1 0 0 1 1-1h3.5a1 1 0 0 1 1 1c0 1.25.2 2.45.57 3.6a1 1 0 0 1-.25 1z" fill="#1b2f6b"/></svg>
      </span>
      <span class="contact-rule__icon">
        <svg width="20" height="20" viewBox="0 0 24 24" aria-hidden="true"><rect x="3" y="5" width="18" height="14" rx="1.5" fill="none" stroke="#1b2f6b" stroke-width="2"/><path d="M3 6l9 7 9-7" fill="none" stroke="#1b2f6b" stroke-width="2"/></svg>
      </span>
      <span class="contact-rule__icon">
        <svg width="20" height="20" viewBox="0 0 24 24" aria-hidden="true"><circle cx="12" cy="12" r="9" fill="none" stroke="#1b2f6b" stroke-width="2"/><path d="M3 12h18M12 3c3 3 3 15 0 18M12 3c-3 3-3 15 0 18" fill="none" stroke="#1b2f6b" stroke-width="1.6"/></svg>
      </span>
      <span class="contact-rule__line"></span>
    </div>
    <div class="contact-list">
      <p class="contact-list__phone">800-555-0147</p>
      <p class="contact-list__line">dorian@oakpartners.example</p>
      <p class="contact-list__line">www.oakpartners.example</p>
    </div>
  </section>

  <section class="card card--back" aria-label="Business card back">
    <div class="pitch">
      <p class="pitch__firm">THE OAK PARTNERS®</p>
      <p class="pitch__headline">INJURED?</p>
      <p class="pitch__call">CALL THE OAK PARTNERS!</p>
      <p class="pitch__phone">(800) 555-0147</p>
    </div>
  </section>
</main>
</body>
</html>
```